Marwick Biomedical Research Institute (MBRI) Web Design

MBRI is a non-profit organization focused on saving the lives of terminally ill patients by becoming the leaders in cutting-edge research, innovative technologies, utilizing national and international partnerships as well as the associated allopathic and naturopathic treatments necessary to do so.

Our primary focus is raising funds to support the research and acquisition of new technologies for life saving treatments which are NOT a one size fits all approach like conventional medicine but rather a marriage of the latest technologies used in combination with other new treatment possibilities for a successful end result.

Our domain is marwickbri.org

Logo files are attached.

Looking for something clean, light, healthy.

Target Market(s)

The site should look and feel towards research/scientific grant writing.
Medical professionals, Medical Scientists.

Industry/Entity Type

Medical And Science

Number of Pages Required

4 page

Requirements
Nice to have
• Here are examples of sites I like in the order of how much I like them.
• https://www.palvorn.org/give.html
• https://www.thekqtf.org/donate-to-kqtf
• https://www.veltrasound.org/we-are-vsf/join-the-cause
• https://www.orvenly.org/involved/donate.html
• https://give.zdkt.org/checkout/donation?eid=58217
• https://www.quimbrel.org/how-you-can-help
• https://donate3.orvenly.org/

```html
<!DOCTYPE html>
<html lang="en">
<head>
<meta charset="utf-8">
<title>Marwick Biomedical Research Institute</title>
<link rel="stylesheet" href="https://fonts.googleapis.com/css2?family=Open+Sans:wght@300;400;600;700&display=swap">
<style>
:root{
  --blue:#1877bf;
  --blue-deep:#0a6cb8;
  --ink:#333b44;
  --muted:#666d74;
  --line:#c9cdd2;
  --footer:#efefef;
  --white:#ffffff;
}
*{box-sizing:border-box;margin:0;padding:0}
html,body{width:1200px;height:2442px;overflow:hidden}
body{position:relative;font-family:"Open Sans",Arial,sans-serif;color:var(--ink);background:var(--white)}
.abs{position:absolute}

/* header */
.site-header{left:0;top:0;width:1200px;height:77px;background:var(--white)}
.brand-name{font-size:15px;font-weight:600;color:var(--ink);letter-spacing:.5px;text-transform:uppercase;white-space:nowrap}
.header-brand{left:160px;top:28px}
.main-nav{left:432px;top:28px;display:flex;gap:29px;font-size:13px;color:#4a5159;text-transform:uppercase}
.main-nav .active{color:var(--blue)}

/* hero */
.hero-photo{left:599px;top:77px;width:601px;height:589px;background:linear-gradient(120deg,#dfe4e8 0%,#f1ede6 45%,#c9b6a0 100%)}
.hero-panel{left:0;top:77px;width:599px;height:589px;background:linear-gradient(160deg,#3a90cc,#1f76b8)}
.hero-title{left:160px;top:196px;width:440px;font-size:42px;font-weight:300;line-height:57px;color:var(--white)}
.hero-text{left:160px;top:328px;width:400px;font-size:16.5px;line-height:28px;color:var(--white)}
.btn-outline{display:flex;align-items:center;justify-content:center;border:1.5px solid rgba(255,255,255,.85);border-radius:28px;color:var(--white);text-transform:uppercase}
.hero-btn{left:160px;top:469px;width:356px;height:54px;font-size:17px}
.slider-arrow{top:343px;width:50px;height:50px}

/* intro */
.intro-title{left:0;top:722px;width:1200px;text-align:center;font-size:24px;font-weight:400;color:var(--blue);text-transform:uppercase}
.intro-sub{left:0;top:766px;width:1200px;text-align:center;font-size:15px;color:var(--ink);text-transform:uppercase}
.intro-divider{left:545px;top:797px}
.intro-text{left:300px;top:814px;width:600px;text-align:center;font-size:12.5px;line-height:19px;color:var(--muted)}
.intro-link{left:0;top:861px;width:1200px;text-align:center;font-size:12.5px;color:var(--blue-deep);text-decoration:underline}

/* about */
.about-item{left:161px;width:354px}
.about-item h3{font-size:13px;font-weight:400;color:var(--ink);text-transform:uppercase;margin-bottom:9px}
.about-item p{font-size:10.5px;line-height:18px;color:var(--muted)}
.about-rule{left:161px;width:354px;border-top:1.5px dotted #9aa0a6}
.video{left:568px;top:944px;width:471px;height:310px;background:linear-gradient(110deg,#cfd6dc,#ece7e2 55%,#c8b8a8)}
.video-frame{left:27px;top:37px;width:418px;height:254px;border:1px solid rgba(255,255,255,.6)}

/* cause band */
.cause-band{left:0;top:1333px;width:1200px;height:375px;background:linear-gradient(90deg,#aab6c0,#c8cfd5 50%,#b7aea4)}
.cause-frame{left:160px;top:1403px;width:314px;height:220px;background:var(--blue)}
.cause-photo{left:170px;top:1411px;width:320px;height:224px;background:linear-gradient(110deg,#c7ccd0,#ebe6e0 60%,#cbbcad);border:1px solid #fff}
.cause-title{left:636px;top:1418px;font-size:33px;font-weight:300;line-height:49px;color:var(--white)}
.cause-btn{top:1542px;height:52px;font-size:14px}

/* patient */
.patient{left:0;top:1708px;width:1200px;height:252px;background:linear-gradient(90deg,#fff,#f6f3f0 50%,#fff)}
.patient-title{left:0;top:1772px;width:1200px;text-align:center;font-size:26px;font-weight:400;color:#222}
.patient-text{left:250px;top:1832px;width:700px;text-align:center;font-size:12px;line-height:19.5px;color:var(--muted)}

/* monthly */
.monthly{left:0;top:1960px;width:1200px;height:140px;background:linear-gradient(90deg,#0f6db8,#1a7ccb 50%,#0f6db8)}
.monthly-title{left:160px;top:1990px;font-size:22px;font-weight:600;color:var(--white)}
.monthly-text{left:160px;top:2020px;width:570px;font-size:17px;line-height:24px;color:var(--white)}
.monthly-btn{left:760px;top:2014px;width:279px;height:50px;font-size:16px}

/* footer */
.site-footer{left:0;top:2100px;width:1200px;height:342px;background:var(--footer)}
.footer-brand{left:0;top:2150px;width:1200px;text-align:center}
.footer-address{left:0;top:2224px;width:1200px;display:flex;justify-content:center;gap:10px;font-size:12px;line-height:18px;color:var(--ink)}
.footer-phone{left:0;top:2273px;width:1200px;display:flex;justify-content:center;align-items:center;gap:8px;font-size:12.5px;color:var(--ink)}
.social{left:487px;top:2323px;display:flex;gap:10px}
.social span{width:39px;height:39px;border-radius:2px}
.copyright{left:0;top:2387px;width:1200px;text-align:center;font-size:10.5px;color:var(--muted)}
</style>
</head>
<body>

<header class="abs site-header">
  <div class="abs brand-name header-brand">Marwick Biomedical</div>
  <nav class="abs main-nav">
    <span class="active">About Us</span><span>Care &amp; Treatment</span><span>Research</span><span>Training</span><span>Get Involved</span><span>Way to Give</span>
  </nav>
</header>

<section>
  <div class="abs hero-photo" role="img" aria-label="Photo of a smiling female doctor with a stethoscope"></div>
  <div class="abs hero-panel" role="img" aria-label="Blue tinted photo of a doctor with a patient"></div>
  <h1 class="abs hero-title">YOUR CONTRIBUTION EXTENDS LIVES</h1>
  <p class="abs hero-text">Make the biggest impact possible by supporting innovative immunotherapy research for all types of disease. Together, we can change the way disease is treated and cured.</p>
  <a class="abs btn-outline hero-btn">Donate Now</a>
  <svg class="abs slider-arrow" style="left:32px" viewBox="0 0 50 50"><circle cx="25" cy="25" r="23.5" fill="none" stroke="#fff" stroke-width="2"/><path d="M28 17 L20 25 L28 33" fill="none" stroke="#fff" stroke-width="3"/></svg>
  <svg class="abs slider-arrow" style="left:1118px" viewBox="0 0 50 50"><circle cx="25" cy="25" r="23.5" fill="none" stroke="#fff" stroke-width="2"/><path d="M22 17 L30 25 L22 33" fill="none" stroke="#fff" stroke-width="3"/></svg>
</section>

<section>
  <h2 class="abs intro-title">Donate the Marwick Biomedical Research Institute</h2>
  <p class="abs intro-sub">Biomedical Research Institute</p>
  <svg class="abs intro-divider" width="110" height="6" viewBox="0 0 110 6"><line x1="0" y1="3" x2="50" y2="3" stroke="#c9cdd2"/><circle cx="55" cy="3" r="2.5" fill="#1877bf"/><line x1="60" y1="3" x2="110" y2="3" stroke="#c9cdd2"/></svg>
  <p class="abs intro-text">Your gift means we can bring hope to medical patients. Together we are fighting disease smarter, better and harder than we ever have before. Thank you for your support.</p>
  <a class="abs intro-link">Donate Now</a>
</section>

<section>
  <div class="abs about-item" style="top:940px"><h3>We are the Biomedical Research Institute</h3><p>Lorem ipsum dolor sit amet, consectetur adipiscing elit, sed do eiusmod tempor incididunt ut labore et dolore magna aliqua. Ut enim ad minim veniam, quis nostrud exercitation ullamco laboris nisi ut aliquip ex ea</p></div>
  <div class="abs about-rule" style="top:1044px"></div>
  <div class="abs about-item" style="top:1067px"><h3>Why support MBRI</h3><p>Lorem ipsum dolor sit amet, consectetur adipiscing elit, sed do eiusmod tempor incididunt ut labore et dolore magna aliqua.</p></div>
  <div class="abs about-rule" style="top:1154px"></div>
  <div class="abs about-item" style="top:1176px"><h3>Our Stories</h3><p>Lorem ipsum dolor sit amet, consectetur adipiscing elit, sed do eiusmod tempor incididunt ut labore et dolore magna aliqua.</p></div>

  <div class="abs video" role="img" aria-label="Video still of a smiling patient in a headscarf">
    <div class="abs video-frame"></div>
    <svg class="abs" style="left:195px;top:130px" width="80" height="50" viewBox="0 0 80 50"><rect width="80" height="50" fill="rgba(60,60,60,.55)"/><path d="M32 14 L52 25 L32 36Z" fill="#fff"/></svg>
    <svg class="abs" style="left:29px;top:260px" width="414" height="28" viewBox="0 0 414 28"><rect x="2" y="2" width="28" height="22" fill="rgba(80,80,80,.5)"/><path d="M12 8 L21 13 L12 18Z" fill="#fff"/><rect x="306" y="2" width="106" height="22" fill="rgba(80,80,80,.5)"/><rect x="314" y="9" width="12" height="8" rx="2" fill="none" stroke="#fff"/><path d="M336 10h4l4-3v12l-4-3h-4z" fill="#fff"/><circle cx="364" cy="13" r="4" fill="#fff"/><rect x="382" y="8" width="16" height="10" fill="none" stroke="#fff"/></svg>
  </div>
</section>

<section>
  <div class="abs cause-band" role="img" aria-label="Blurred photo of a hospital waiting room"></div>
  <div class="abs cause-frame"></div>
  <div class="abs cause-photo" role="img" aria-label="Photo of a smiling patient in a headscarf"></div>
  <h2 class="abs cause-title">One Cause to Cure<br>Mbri Marwick Biomedical</h2>
  <a class="abs btn-outline cause-btn" style="left:632px;width:174px">Get Involved</a>
  <a class="abs btn-outline cause-btn" style="left:816px;width:190px">Donate Now</a>
</section>

<section>
  <div class="abs patient" role="img" aria-label="Faint photo of a smiling patient"></div>
  <h2 class="abs patient-title">MEET OUR PATIENT</h2>
  <p class="abs patient-text">Lorem ipsum dolor sit amet, consectetur adipiscing elit, sed do eiusmod tempor incididunt ut labore et dolore magna aliqua. Ut enim ad minim veniam, quis nostrud exercitation ullamco laboris nisi ut aliquip ex ea commodo consequat. Duis aute irure dolor in reprehenderit in voluptate velit esse cillum dolore eu fugiat nulla pariatur.</p>
</section>

<section>
  <div class="abs monthly"></div>
  <h2 class="abs monthly-title">Become a monthly donor</h2>
  <p class="abs monthly-text">When you become a Mbri Partners In Hope monthly donor,your gift means Mbri has the freedom to focus on what matters most saving...</p>
  <a class="abs btn-outline monthly-btn">Become a Monthly Donor</a>
</section>

<footer>
  <div class="abs site-footer" role="img" aria-label="Faint world map background"></div>
  <div class="abs brand-name footer-brand">Marwick Biomedical</div>
  <div class="abs footer-address">
    <svg width="14" height="22" viewBox="0 0 14 22"><path d="M7 0C3 0 0 3 0 7c0 5 7 15 7 15s7-10 7-15c0-4-3-7-7-7z" fill="#1877bf"/><circle cx="7" cy="7" r="2.5" fill="#efefef"/></svg>
    <span>Lorem Ipsum Dolor Sit Amet Consectetur<br>Dolor Sit Amet Consectetur</span>
  </div>
  <div class="abs footer-phone">
    <svg width="14" height="14" viewBox="0 0 14 14"><path d="M3 1 L6 4 L4 6 Q6 9 8 10 L10 8 L13 11 L11 13 Q5 13 1 3Z" fill="#1877bf"/></svg>
    <span>0012-345-567 &nbsp;/&nbsp; 0012-345-567</span>
  </div>
  <div class="abs social" aria-label="Social links">
    <span style="background:#3b5998"></span><span style="background:#1da1f2"></span><span style="background:#dd4b39"></span><span style="background:#0e76a8"></span><span style="background:#cb2027"></span>
  </div>
  <p class="abs copyright">Copyrights©2017 Mbri Allrights are Resrved</p>
</footer>

</body>
</html>
```